SkyvornQ Business Cards and Stationary Design

Need a design for our business cards and stationary. I want to carry on the theme of the logo. I want the business cards to have a design on the back. I would like the business cards and the stationary to carry the same theme, design scheme, and branding

Target Market(s)

Airlines and Maintenance Facilities

Industry/Entity Type

Aviation

Contact Information for Business Card

Name
Position Title
Address: 4827 Trellis Hollow Road, Fort Pierce, Florida, 34951
Office Number
Mobile Number
Email
Website

Font styles to use
Serif
Sans Serif

Colors

Designer to choose colors to be used in the design.

```html
<!DOCTYPE html>
<html lang="en">
<head>
<meta charset="utf-8">
<title>SkyvornQ Business Card</title>
<link rel="stylesheet" href="https://fonts.googleapis.com/css2?family=Oswald:wght@500&family=Work+Sans:wght@400;600&display=swap">
<style>
  :root {
    --backdrop: #232323;
    --card: #1b1b1c;
    --card-edge: #2a2a2b;
    --ink: #f2f2f2;
    --accent: #1e9be0;
  }
  * { margin: 0; padding: 0; box-sizing: border-box; }
  html, body { width: 1200px; height: 900px; overflow: hidden; }
  body {
    background: var(--backdrop);
    font-family: "Work Sans", sans-serif;
    color: var(--ink);
    position: relative;
  }
  .card {
    position: absolute;
    left: 280px;
    width: 640px;
    height: 366px;
    background: linear-gradient(135deg, #151516 0%, var(--card) 55%, #262627 100%);
    border: 1px solid var(--card-edge);
    box-shadow: 0 10px 30px rgba(0,0,0,0.55);
  }
  .card--front { top: 64px; }
  .card--back { top: 466px; }

  .brand {
    position: absolute;
    inset: 0;
    display: flex;
    align-items: center;
    justify-content: center;
  }
  .brand__name {
    font-weight: 600;
    font-size: 48px;
    letter-spacing: 8px;
    color: var(--ink);
  }

  .person {
    position: absolute;
    right: 360px;
    top: 124px;
    text-align: right;
  }
  .person__name {
    font-family: "Oswald", sans-serif;
    font-weight: 500;
    font-size: 32px;
    line-height: 1;
    color: var(--accent);
    text-transform: uppercase;
    white-space: nowrap;
  }
  .person__title {
    margin-top: 6px;
    font-size: 17px;
    color: var(--ink);
  }
  .divider {
    position: absolute;
    left: 300px;
    top: 114px;
    width: 2px;
    height: 90px;
    background: var(--ink);
  }
  .contact {
    position: absolute;
    left: 322px;
    top: 114px;
    list-style: none;
    font-size: 17px;
    line-height: 22.5px;
  }
  .contact li { display: flex; align-items: center; gap: 10px; white-space: nowrap; }
  .contact svg { width: 12px; height: 12px; flex: none; }
  .contact__highlight { color: var(--accent); font-weight: 600; }
  .address {
    position: absolute;
    left: 92px;
    top: 286px;
    font-size: 18px;
    letter-spacing: 0.3px;
    white-space: nowrap;
  }
</style>
</head>
<body>
  <section class="card card--front">
    <div class="brand">
      <div class="brand__name">SkyvornQ</div>
    </div>
  </section>

  <section class="card card--back">
    <div class="person">
      <div class="person__name">Dorian Ashcroft</div>
      <div class="person__title">Director</div>
    </div>
    <div class="divider"></div>
    <ul class="contact">
      <li>
        <svg viewBox="0 0 12 12" aria-hidden="true"><path d="M2.5 1 L4.5 1 L5.2 3.6 L4 4.6 C4.6 6 5.9 7.4 7.4 8 L8.4 6.8 L11 7.5 L11 9.5 C11 10.4 10.3 11 9.4 11 C4.8 10.6 1.4 7.2 1 2.6 C1 1.7 1.6 1 2.5 1 Z" fill="var(--accent)"/></svg>
        513-555-0192
      </li>
      <li>
        <svg viewBox="0 0 12 12" aria-hidden="true"><rect x="3" y="0.8" width="6" height="10.4" rx="1.2" fill="none" stroke="var(--accent)" stroke-width="1.2"/><circle cx="6" cy="9.2" r="0.7" fill="var(--accent)"/></svg>
        513-555-0178
      </li>
      <li>
        <svg viewBox="0 0 12 12" aria-hidden="true"><rect x="1" y="2.5" width="10" height="7" fill="none" stroke="var(--accent)" stroke-width="1.2"/><path d="M1 2.8 L6 6.6 L11 2.8" fill="none" stroke="var(--accent)" stroke-width="1.2"/></svg>
        info@skyvornq.com
      </li>
      <li>
        <svg viewBox="0 0 12 12" aria-hidden="true"><circle cx="6" cy="6" r="5" fill="none" stroke="var(--accent)" stroke-width="1.1"/><ellipse cx="6" cy="6" rx="2.2" ry="5" fill="none" stroke="var(--accent)" stroke-width="1"/><path d="M1 6 H11" stroke="var(--accent)" stroke-width="1"/></svg>
        <span>www.<span class="contact__highlight">skyvornq</span>.com</span>
      </li>
    </ul>
    <p class="address">4827 Trellis Hollow Road, Fort Pierce, Florida, 34951</p>
  </section>
</body>
</html>
```